Breakfast Cafe - The Sunny Nook

It is for my breakfast and lunch cafe with a hawaiian / beach theme. I am open 7 days a week from 7am to 2pm. We serve traditional American food such as omelettes, pancakes, burgers and sandwiches. I'll upload my old card and my new logo to be used. We have a lot of day to day regulars who eat there during the week, our t-shirts actually say 'Locals Only' on them. Hope this helps. Thanks.

Target Market(s)

anyone who has an appetite!

Industry/Entity Type

American Restaurant

Contact Information for Business Card

4815C Marlow Grove Avenue
Long Beach, California
(555) 731-2294

Requirements
Must have
• Address and phone number easily readable.
Nice to have
• beach or tropical theme

```html
<!DOCTYPE html>
<html lang="en">
<head>
<meta charset="utf-8">
<title>The Sunny Nook – Business Card</title>
<link rel="stylesheet" href="https://fonts.googleapis.com/css2?family=Bebas+Neue&family=Kaushan+Script&display=swap">
<style>
  :root {
    --backdrop: #1e1e1e;
    --card: #f6ecd9;
    --brown: #a8560f;
    --sky: #58b9d4;
    --red: #cf1240;
    --tiki-light: #e6c9a0;
    --tiki-dark: #d9b484;
  }
  html, body {
    margin: 0;
    width: 1200px;
    height: 960px;
    overflow: hidden;
    background: var(--backdrop);
  }
  .card {
    position: absolute;
    left: 300px;
    top: 309px;
    width: 600px;
    height: 343px;
    border-radius: 22px;
    background: var(--card);
    overflow: hidden;
    font-family: "Bebas Neue", "Arial Narrow", sans-serif;
  }
  .tiki-decoration {
    position: absolute;
    left: 0;
    top: 0;
    width: 195px;
    height: 343px;
    opacity: 0.55;
  }
  .address {
    position: absolute;
    left: 40px;
    top: 36px;
    margin: 0;
    color: var(--brown);
    font-size: 25px;
    line-height: 25px;
  }
  .phone {
    position: absolute;
    left: 40px;
    top: 89px;
    margin: 0;
    color: var(--sky);
    font-size: 31px;
    line-height: 32px;
  }
  .brand {
    position: absolute;
    left: 397px;
    top: 31px;
    width: 166px;
    height: 170px;
    display: flex;
    flex-direction: column;
    align-items: center;
    justify-content: center;
    gap: 12px;
  }
  .brand-dot {
    width: 96px;
    height: 96px;
    border-radius: 50%;
    background: var(--brown);
  }
  .brand-name {
    margin: 0;
    color: var(--brown);
    font-size: 30px;
    line-height: 30px;
    white-space: nowrap;
  }
  .tagline {
    position: absolute;
    left: 40px;
    top: 252px;
    margin: 0;
    color: var(--brown);
    font-family: "Kaushan Script", cursive;
    font-size: 40px;
    line-height: 60px;
  }
  .details {
    position: absolute;
    right: 40px;
    top: 244px;
    text-align: right;
  }
  .details p { margin: 0; }
  .details .kind { color: var(--brown); font-size: 26px; line-height: 26px; }
  .details .hours { color: var(--sky); font-size: 20px; line-height: 22px; }
  .details .menu { color: var(--red); font-size: 16px; line-height: 20px; }
</style>
</head>
<body>
  <div class="card">
    <svg class="tiki-decoration" viewBox="0 0 195 343" role="img" aria-label="Faint carved tiki figure holding a coffee mug">
      <defs>
        <linearGradient id="tikiFade" x1="0" y1="0" x2="1" y2="0">
          <stop offset="0" stop-color="var(--tiki-dark)"/>
          <stop offset="1" stop-color="var(--tiki-light)" stop-opacity="0.4"/>
        </linearGradient>
      </defs>
      <rect x="0" y="0" width="195" height="343" fill="url(#tikiFade)"/>
    </svg>

    <p class="address">4815C Marlow Grove Avenue<br>Long Beach, California</p>
    <p class="phone">P.(555) 731-2294</p>

    <div class="brand">
      <div class="brand-dot"></div>
      <p class="brand-name">The Sunny Nook</p>
    </div>

    <p class="tagline">Locals Only</p>

    <div class="details">
      <p class="kind">Breakfast &amp; Lunch Cafe</p>
      <p class="hours">Open 7 days a week from 7am to 2pm.</p>
      <p class="menu">Serving traditional American food</p>
    </div>
  </div>
</body>
</html>
```